Meridale Bed Company Needs Business Card

Looking for a very nice looking business card. Creative but not extravagant. We sell beds and pillows across the U.S. and need something professional but catchy. I have attached the logo.

Name : Devin Holt
Title : President
Phone : (800) 471-2960
Email: sleep@quilmora.com
Website: www.quilmora.com

Can be single-sided or double-sided
horizontal or vertical

Can use Blues/Greys

Target Market(s)

Mass Market

Industry/Entity Type

Retail

Contact Information for Business Card

Name : Devin Holt
Title : President
Phone : (800) 471-2960
Email: sleep@quilmora.com
Website: www.quilmora.com

Requirements
Must have
• Clean, Modern, Smooth
• Can use Blues/Greys
• On the other side without the information - have something simple like www.quilmora.com or our logo
Nice to have
• Surprise me
Should not have
• Nothing crazy, nothing cluttered

```html
<!DOCTYPE html>
<html lang="en">
<head>
<meta charset="utf-8">
<title>Quilmora Business Card</title>
<link href="https://fonts.googleapis.com/css2?family=Lato:wght@300;400;700&display=swap" rel="stylesheet">
<style>
  :root {
    --stage: #2e2d2c;
    --card-dark: #4a4a4a;
    --card-light: #eef1f4;
    --brand-blue: #3a9fd6;
    --ink: #3b3b3b;
    --white: #ffffff;
  }
  * { box-sizing: border-box; margin: 0; padding: 0; }
  html, body {
    width: 1200px;
    height: 810px;
    overflow: hidden;
    background: var(--stage);
    font-family: "Lato", sans-serif;
  }
  .stage {
    position: relative;
    width: 1200px;
    height: 810px;
    display: flex;
    align-items: center;
    justify-content: center;
    gap: 40px;
  }
  .card {
    position: relative;
    width: 520px;
    height: 300px;
    border-radius: 18px;
    display: flex;
    flex-direction: column;
    align-items: center;
    box-shadow: 0 10px 30px rgba(0,0,0,0.35);
  }
  .wordmark {
    font-family: "Lato", sans-serif;
    font-weight: 300;
    color: var(--brand-blue);
    letter-spacing: 1px;
    line-height: 1;
  }
  /* Back side */
  .card--back { background: var(--card-dark); }
  .card--back .wordmark {
    font-size: 62px;
    margin-top: 92px;
  }
  .card--back .web {
    position: absolute;
    bottom: 58px;
    font-size: 12px;
    color: var(--white);
    letter-spacing: 0.3px;
  }
  /* Front side */
  .card--front { background: var(--card-light); }
  .card--front .wordmark {
    font-size: 58px;
    margin-top: 58px;
  }
  .holder { margin-top: 26px; text-align: center; }
  .holder__name {
    font-size: 16px;
    font-weight: 700;
    color: var(--brand-blue);
  }
  .holder__title {
    font-size: 12px;
    color: var(--ink);
    margin-top: 2px;
  }
  .contacts {
    position: absolute;
    bottom: 40px;
    display: flex;
    gap: 10px;
    font-size: 13px;
    color: var(--ink);
  }
  .contact { display: flex; align-items: center; gap: 3px; }
  .contact__badge { width: 16px; height: 16px; flex: none; }
</style>
</head>
<body>
<main class="stage">
  <section class="card card--back" aria-label="Business card back">
    <div class="wordmark">quilmora</div>
    <div class="web">www.quilmora.com</div>
  </section>

  <section class="card card--front" aria-label="Business card front">
    <div class="wordmark">quilmora</div>
    <div class="holder">
      <div class="holder__name">Devin Holt</div>
      <div class="holder__title">President</div>
    </div>
    <div class="contacts">
      <span class="contact">
        <svg class="contact__badge" viewBox="0 0 16 16" aria-hidden="true">
          <circle cx="8" cy="8" r="7" fill="none" stroke="var(--brand-blue)" stroke-width="1.2"/>
          <text x="8" y="11.5" text-anchor="middle" font-size="9.5" font-family="Lato, sans-serif" fill="var(--brand-blue)">P</text>
        </svg>
        (800) 471-2960
      </span>
      <span class="contact">
        <svg class="contact__badge" viewBox="0 0 16 16" aria-hidden="true">
          <circle cx="8" cy="8" r="7" fill="none" stroke="var(--brand-blue)" stroke-width="1.2"/>
          <text x="8" y="11.5" text-anchor="middle" font-size="9.5" font-family="Lato, sans-serif" fill="var(--brand-blue)">E</text>
        </svg>
        sleep@quilmora.com
      </span>
      <span class="contact">
        <svg class="contact__badge" viewBox="0 0 16 16" aria-hidden="true">
          <circle cx="8" cy="8" r="7" fill="none" stroke="var(--brand-blue)" stroke-width="1.2"/>
          <text x="8" y="11.5" text-anchor="middle" font-size="9" font-family="Lato, sans-serif" fill="var(--brand-blue)">W</text>
        </svg>
        www.quilmora.com
      </span>
    </div>
  </section>
</main>
</body>
</html>
```